Thornvale Group needs a business card design

We need a new business card design using the logo recently selected in a logo competition on Pixel Bazaar. Our business is a consultancy specializing in aviation and energy and the winning business card design will promote an image of precision and professionalism with creativity.

Please use the logo with the name on the front of the card and use a complementary font. Make the back white with either the light grey or dark grey logo.

Target Market(s)

Senior finance and legal leaders at aviation and energy companies

Industry/Entity Type

Management Consulting

Contact Information for Business Card

Peter Castrell
President
Thornvale Group

www.thornvalegroup.example

(555) 204-6391
pc@thornvalegroup.example

Requirements
Must have
• Professional font that goes well with the logo font

```html
<!DOCTYPE html>
<html lang="en">
<head>
<meta charset="utf-8">
<title>Thornvale Group – Business Card</title>
<link rel="stylesheet" href="https://fonts.googleapis.com/css2?family=Open+Sans:wght@300;400;700&display=swap">
<style>
  :root{
    --navy:#0d3f6e;
    --navy-deep:#06284d;
    --navy-light:#2f6d98;
    --ink:#14406b;
    --grey:#6d6f72;
    --white:#ffffff;
    --stage:#e9eaec;
  }
  *{box-sizing:border-box;margin:0;padding:0}
  html,body{width:1200px;height:913px;overflow:hidden;background:var(--stage);font-family:"Open Sans",Arial,sans-serif}
  .canvas{position:relative;width:1200px;height:913px}
  .card{position:absolute;width:520px;height:297px;overflow:hidden;box-shadow:0 6px 18px rgba(0,0,0,.18)}
  .card--front{left:50px;top:308px;background:var(--white)}
  .card--back{left:630px;top:308px;background:linear-gradient(160deg,var(--navy-light) 0%,var(--navy) 45%,var(--navy-deep) 100%)}

  .card__shapes{position:absolute;inset:0;width:100%;height:100%}

  .brand{position:absolute;display:flex;align-items:center;gap:10px;font-weight:400;letter-spacing:.18em;line-height:1.25}
  .brand__mark{width:14px;height:14px;flex:none}
  .brand--front{left:34px;top:132px;color:var(--ink);font-size:19px}
  .brand--front .brand__mark{background:var(--ink)}
  .brand--back{left:120px;top:120px;color:var(--white);font-size:28px}
  .brand--back .brand__mark{width:20px;height:20px;background:var(--white)}

  .holder{position:absolute;right:34px;top:70px;text-align:right}
  .holder__name{font-weight:700;font-size:19px;color:var(--ink)}
  .holder__title{margin-top:6px;font-size:12px;font-weight:400;color:var(--grey)}

  .contact{position:absolute;left:34px;top:214px;list-style:none;font-size:12.5px;color:var(--ink);line-height:1.5}
  .contact li{display:flex;align-items:center;gap:8px}
  .contact svg{width:11px;height:11px;flex:none}
</style>
</head>
<body>
<main class="canvas">

  <section class="card card--front" aria-label="Card front">
    <svg class="card__shapes" viewBox="0 0 520 297" aria-hidden="true">
      <line x1="34" y1="104" x2="486" y2="104" stroke="var(--ink)" stroke-width="1.2"/>
      <line x1="34" y1="200" x2="250" y2="200" stroke="var(--ink)" stroke-width="1.2"/>
      <polygon points="290,238 520,238 520,297 304,297 304,262 290,262" fill="var(--navy)"/>
    </svg>

    <div class="holder">
      <p class="holder__name">Peter Castrell</p>
      <p class="holder__title">President</p>
    </div>

    <div class="brand brand--front">
      <span class="brand__mark"></span>
      <span>THORNVALE<br>GROUP</span>
    </div>

    <ul class="contact">
      <li>
        <svg viewBox="0 0 12 12"><path d="M3 1 L5 3.5 L4 5 Q5 7 7 8 L8.5 7 L11 9 L10 11 Q5 11 1 3 Z" fill="var(--ink)"/></svg>
        (555) 204-6391
      </li>
      <li>
        <svg viewBox="0 0 12 12"><rect x="1" y="2.5" width="10" height="7" fill="none" stroke="var(--ink)" stroke-width="1.1"/><path d="M1 2.5 L6 6.5 L11 2.5" fill="none" stroke="var(--ink)" stroke-width="1.1"/></svg>
        pc@thornvalegroup.example
      </li>
      <li>
        <svg viewBox="0 0 12 12"><circle cx="6" cy="6" r="5" fill="none" stroke="var(--ink)" stroke-width="1.1"/><ellipse cx="6" cy="6" rx="2.2" ry="5" fill="none" stroke="var(--ink)" stroke-width="1"/><line x1="1" y1="6" x2="11" y2="6" stroke="var(--ink)" stroke-width="1"/></svg>
        www.thornvalegroup.example
      </li>
    </ul>
  </section>

  <section class="card card--back" aria-label="Card back">
    <svg class="card__shapes" viewBox="0 0 520 297" aria-hidden="true">
      <polygon points="0,238 230,238 230,262 244,262 244,297 0,297" fill="var(--white)"/>
    </svg>
    <div class="brand brand--back">
      <span class="brand__mark"></span>
      <span>THORNVALE<br>GROUP</span>
    </div>
  </section>

</main>
</body>
</html>
```